Heron Dusk business card design

I make handmade colourful women's beaded jewellery (necklaces and earnings).
I require a business card to be designed to truly reflect my jewellery, that is, it is different and stands out.
I would like the business card to look creative, arty, gentle and feminine and fit in with the look of my website and logo (already developed).
I would like the business card to have strong use of the water reeds that are flowing in the wind (please see the banner image on my website www.herondusk.net and attached files).

Target Market(s)

Women who are fashion conscious, hip and funky. My audience like things that are a little different and stand out in a crowd.These women are aged in their 20's-40's.

Industry/Entity Type

Jewelry

Contact Information for Business Card

Please include the following items:
1) my logo: Heron Dusk
2) my name, address and phone number: Darla Fontenot, Sydney, Australia, 0498 315 270
3) my web details: www.herondusk.net, info@herondusk.net, www.wavelink.net/herondusk

Font styles to use
Other font styles liked:
• Remachine Script

Requirements
Must have
• My business card must have the following:
• 1) my personal details including all my website contacts (see above).
• 2) Heron Dusk logo
• 3) Reeds flowing in the wind (see my banner image on my website www.herondusk.net or see attached files).
Nice to have
• A sunrise in the background (rising over water)
• I would prefer that the colour scheme to fit with the Heron Dusk logo, that is the colours of an early morning sunrise i.e yellows, oranges. The use of black and white is fine.
Should not have
• I do not like a commercial manufactured look with hard edges. I would like a look that is soft and reflects an artistic, creative and independent business.

```html
<!DOCTYPE html>
<html lang="en">
<head>
<meta charset="utf-8">
<title>Heron Dusk — Business Card</title>
<link rel="stylesheet" href="https://fonts.googleapis.com/css2?family=Arimo:wght@400&display=swap">
<style>
  :root{
    --stage:#ebe8e4;
    --card:#ffffff;
    --reed-light:#f1f1f1;
    --reed-mid:#c9c9c9;
    --sun:#f3b313;
    --accent:#f2ad17;
    --ink:#1d1d1d;
  }
  *{margin:0;padding:0;box-sizing:border-box}
  html,body{width:1200px;height:902px;overflow:hidden}
  body{background:var(--stage);font-family:"Arimo",Arial,sans-serif;position:relative}
  .card{position:absolute;left:80px;top:154px;width:1040px;height:594px;background:var(--card);
        box-shadow:0 6px 24px rgba(0,0,0,.18);overflow:hidden}
  .card-art{position:absolute;inset:0}
  .brand{position:absolute;left:60px;top:70px;width:380px;text-align:center}
  .brand-name{font-size:48px;font-weight:400;color:var(--ink);letter-spacing:1px}
  .brand-sun{display:block;margin:26px auto 0;width:250px;height:250px;border-radius:50%;
             background:var(--sun)}
  .holder-name{position:absolute;right:80px;top:70px;font-size:42px;font-weight:400;color:var(--accent)}
  .contacts{position:absolute;right:40px;top:328px;list-style:none}
  .contacts li{display:flex;justify-content:flex-end;align-items:center;gap:14px;
               height:31px;font-size:23px;color:var(--ink)}
  .contact-icon{width:20px;height:20px;flex:none}
</style>
</head>
<body>
  <section class="card">
    <svg class="card-art" width="1040" height="594" viewBox="0 0 1040 594">
      <defs>
        <linearGradient id="reedTone" x1="0" y1="0" x2="0.6" y2="1">
          <stop offset="0" stop-color="#f1f1f1"/>
          <stop offset="1" stop-color="#c9c9c9"/>
        </linearGradient>
      </defs>
      <path role="img" aria-label="Grey reeds flowing in the wind"
            d="M0 0 H360 C410 120 470 210 480 330 C490 450 515 530 550 594 H0 Z"
            fill="url(#reedTone)"/>
      <path class="accent-band" d="M385 0 C440 120 500 210 510 330 C520 450 545 530 580 594"
            fill="none" stroke="#f2ad17" stroke-width="14"/>
    </svg>

    <div class="brand">
      <div class="brand-name">Heron Dusk</div>
      <span class="brand-sun" role="img" aria-label="Sunrise over water"></span>
    </div>

    <h1 class="holder-name">Darla Fontenot</h1>

    <ul class="contacts">
      <li>0498 315 270
        <svg class="contact-icon" viewBox="0 0 20 20"><rect width="20" height="20" fill="#f2ad17"/><path d="M6 4 L8.5 4 L9.5 7 L8 8.2 Q9.5 11.5 12 12.2 L13.2 10.8 L16 12 L16 14.5 Q9 15 5.5 7 Z" fill="#fff"/></svg>
      </li>
      <li>Marlow Bay, Coralia,
        <svg class="contact-icon" viewBox="0 0 20 20"><rect width="20" height="20" fill="#f2ad17"/><path d="M10 3.5 A4.5 4.5 0 0 1 14.5 8 C14.5 11 10 16.5 10 16.5 C10 16.5 5.5 11 5.5 8 A4.5 4.5 0 0 1 10 3.5 Z" fill="#fff"/><circle cx="10" cy="8" r="1.7" fill="#f2ad17"/></svg>
      </li>
      <li>info@herondusk.net
        <svg class="contact-icon" viewBox="0 0 20 20"><rect width="20" height="20" fill="#f2ad17"/><rect x="4" y="6" width="12" height="8" fill="#fff"/><path d="M4 6 L10 11 L16 6" fill="none" stroke="#f2ad17" stroke-width="1.2"/></svg>
      </li>
      <li>www.herondusk.net
        <svg class="contact-icon" viewBox="0 0 20 20"><rect width="20" height="20" fill="#f2ad17"/><circle cx="10" cy="10" r="5.5" fill="none" stroke="#fff" stroke-width="1.4"/><ellipse cx="10" cy="10" rx="2.3" ry="5.5" fill="none" stroke="#fff" stroke-width="1.2"/><path d="M4.5 10 H15.5" stroke="#fff" stroke-width="1.2"/></svg>
      </li>
      <li>www.wavelink.net/herondusk
        <svg class="contact-icon" viewBox="0 0 20 20"><rect width="20" height="20" fill="#f2ad17"/></svg>
      </li>
    </ul>
  </section>
</body>
</html>
```